Meridale Bed Company Needs Business Card

Looking for a very nice looking business card. Creative but not extravagant. We sell beds and pillows across the U.S. and need something professional but catchy. I have attached the logo.

Name : Devin Holt
Title : President
Phone : (800) 471-2960
Email: sleep@quilmora.com
Website: www.quilmora.com

Can be single-sided or double-sided
horizontal or vertical

Can use Blues/Greys

Target Market(s)

Mass Market

Industry/Entity Type

Retail

Contact Information for Business Card

Name : Devin Holt
Title : President
Phone : (800) 471-2960
Email: sleep@quilmora.com
Website: www.quilmora.com

Requirements
Must have
• Clean, Modern, Smooth
• Can use Blues/Greys
• On the other side without the information - have something simple like www.quilmora.com or our logo
Nice to have
• Surprise me
Should not have
• Nothing crazy, nothing cluttered

```html
<!DOCTYPE html>
<html lang="en">
<head>
<meta charset="utf-8">
<title>Quilmora Business Card</title>
<link rel="stylesheet" href="https://fonts.googleapis.com/css2?family=Quicksand:wght@400&family=Hind:wght@400;500;600&display=swap">
<style>
  :root {
    --backdrop: #dfe2e3;
    --card-white: #ffffff;
    --brand-sky: #4dcff5;
    --ink-white: #ffffff;
    --shadow: rgba(0, 0, 0, 0.28);
  }
  * { margin: 0; padding: 0; box-sizing: border-box; }
  html, body {
    width: 1200px;
    height: 761px;
    overflow: hidden;
    background: var(--backdrop);
  }
  .canvas {
    position: relative;
    width: 1200px;
    height: 761px;
  }
  .card {
    position: absolute;
    box-shadow: 5px 6px 6px var(--shadow);
  }
  .card-front {
    left: 155px;
    top: 271px;
    width: 398px;
    height: 230px;
    background: var(--card-white);
  }
  .card-front .base-band {
    position: absolute;
    left: 0;
    bottom: 0;
    width: 100%;
    height: 6px;
    background: var(--brand-sky);
  }
  .wordmark {
    position: absolute;
    font-family: "Quicksand", sans-serif;
    font-weight: 400;
    line-height: 1;
    white-space: nowrap;
  }
  .card-front .wordmark {
    left: 0;
    width: 100%;
    top: 86px;
    text-align: center;
    font-size: 50px;
    letter-spacing: 1px;
    color: var(--brand-sky);
  }
  .card-back {
    left: 638px;
    top: 271px;
    width: 404px;
    height: 226px;
    background: var(--brand-sky);
    color: var(--ink-white);
    font-family: "Hind", sans-serif;
  }
  .card-back .wordmark {
    left: 46px;
    top: 30px;
    font-size: 40px;
    letter-spacing: 1px;
    color: var(--ink-white);
  }
  .person {
    position: absolute;
    left: 48px;
    top: 102px;
  }
  .person-name {
    font-size: 17px;
    font-weight: 600;
    line-height: 20px;
    letter-spacing: 0.3px;
  }
  .person-title {
    font-size: 18px;
    font-weight: 400;
    line-height: 20px;
    letter-spacing: 0.4px;
  }
  .contact-list {
    position: absolute;
    left: 47px;
    top: 159px;
    list-style: none;
    font-size: 11.5px;
    line-height: 17px;
    letter-spacing: 0.3px;
  }
  .contact-list li,
  .address {
    display: flex;
    align-items: center;
    gap: 10px;
  }
  .icon { flex: none; fill: var(--ink-white); }
  .address {
    position: absolute;
    left: 233px;
    top: 100px;
    align-items: flex-start;
    gap: 6px;
    font-size: 11.5px;
    line-height: 14px;
    letter-spacing: 0.3px;
  }
  .address .icon { margin-top: 1px; }
  .address p { margin-left: -1px; }
  .address .line-two { margin-left: -12px; }
  .website {
    position: absolute;
    left: 233px;
    top: 157px;
    font-size: 13.5px;
    font-weight: 500;
    letter-spacing: 0.6px;
  }
  .social-row {
    position: absolute;
    left: 237px;
    top: 177px;
    display: flex;
    gap: 9px;
  }
  .social-dot {
    width: 14px;
    height: 14px;
    border-radius: 50%;
    background: var(--ink-white);
  }
</style>
</head>
<body>
<main class="canvas">
  <section class="card card-front" aria-label="Card front">
    <div class="wordmark">quilmora</div>
    <div class="base-band"></div>
  </section>

  <section class="card card-back" aria-label="Card back">
    <div class="wordmark">quilmora</div>

    <div class="person">
      <p class="person-name">Devin Holt</p>
      <p class="person-title">President</p>
    </div>

    <ul class="contact-list">
      <li>
        <svg class="icon" width="7" height="10" viewBox="0 0 7 10" aria-hidden="true">
          <path d="M1 0h5a1 1 0 0 1 1 1v8a1 1 0 0 1-1 1H1a1 1 0 0 1-1-1V1a1 1 0 0 1 1-1zm0 1.5v6h5v-6z"/>
        </svg>
        <span>sleep@quilmora.com</span>
      </li>
      <li>
        <svg class="icon" width="9" height="7" viewBox="0 0 9 7" aria-hidden="true">
          <path d="M0 0h9v7H0zm1 1.2v4.8h7V1.2L4.5 3.8z"/>
        </svg>
        <span>(800) 471-2960</span>
      </li>
    </ul>

    <div class="address">
      <svg class="icon" width="6" height="9" viewBox="0 0 6 9" aria-hidden="true">
        <path d="M3 0a3 3 0 0 1 3 3c0 2.2-3 6-3 6S0 5.2 0 3a3 3 0 0 1 3-3zm0 1.8a1.2 1.2 0 1 0 0 2.4 1.2 1.2 0 0 0 0-2.4z"/>
      </svg>
      <p>14 Harlow Lane,<br><span class="line-two">Brookvale NSW 2100</span></p>
    </div>

    <p class="website">www.quilmora.com</p>

    <div class="social-row" aria-label="Social profiles">
      <span class="social-dot"></span>
      <span class="social-dot"></span>
      <span class="social-dot"></span>
      <span class="social-dot"></span>
      <span class="social-dot"></span>
    </div>
  </section>
</main>
</body>
</html>
```